Quick Straightforward Billboard Redesign

- Design billboard sized for 10 foot' x 36' foot width live area size and please include bleeds 6" around all sides
- Exact blue color match is imperative in headline, logo, phone number bubble or wherever used. C-83 / M-45 / Y-1 / K-0-
- What I hope to illustrate is that our company offers the best porch screening in the area area, in regards to quality, expertise, durability, storms proof, but we do not build screen porches.
- Current board is attached below from previous designer, and as you can see sizing was off, white space on edges make it appear to be sized incorrectly.
- I also attached my own little mock up idea well well if it helps, favorite image, logo, headline, etc and ideas perhaps on expanding or making this better?

Thanks so much!

Target Market(s)

Drivers and passengers, Southeastern NC, are of immense new construction and high end homes.

Industry/Entity Type

Construction

Colors
0054AA
0677BA
7BADD7
CADEEF
E8F1F8

Requirements
Must have
• Blue color matching
Nice to have
• Design spins or other thoughts on my little mock up

```html
<!DOCTYPE html>
<html lang="en">
<head>
<meta charset="utf-8">
<title>Tidewater Screening Billboard</title>
<link rel="stylesheet" href="https://fonts.googleapis.com/css2?family=Poppins:wght@800&family=Oswald:wght@600&display=swap">
<style>
  :root {
    --brand-blue: #2B67AA;
    --brand-green: #2E9E4F;
    --board-white: #FFFFFF;
    --stage: #E8F1F8;
    --photo-sky: #9CC3E6;
    --photo-deck: #C9C1B2;
    --photo-wicker: #6E6456;
  }
  html, body {
    margin: 0;
    padding: 0;
    width: 1200px;
    height: 649px;
    overflow: hidden;
    background: var(--stage);
  }
  .billboard {
    position: absolute;
    left: 30px;
    top: 166px;
    width: 1140px;
    height: 317px;
    background: var(--board-white);
    display: flex;
    box-shadow: 0 2px 10px rgba(0, 0, 0, 0.12);
  }
  .porch-photo {
    width: 470px;
    height: 100%;
    flex: none;
    background: linear-gradient(180deg, var(--photo-sky) 0%, #D9E3E6 30%, #8FA67A 45%, var(--photo-deck) 60%, var(--photo-wicker) 100%);
  }
  .message {
    flex: 1;
    position: relative;
    padding: 26px 34px 0 30px;
  }
  .headline {
    margin: 0;
    font-family: "Poppins", sans-serif;
    font-weight: 800;
    font-size: 52px;
    line-height: 1.02;
    letter-spacing: 0.5px;
    text-transform: uppercase;
    white-space: nowrap;
  }
  .headline-top { display: block; color: var(--brand-blue); }
  .headline-bottom { display: block; color: var(--brand-green); }
  .contact-row {
    position: absolute;
    left: 30px;
    right: 34px;
    bottom: 30px;
    display: flex;
    align-items: center;
    justify-content: space-between;
    gap: 18px;
  }
  .brand {
    display: flex;
    align-items: center;
    gap: 14px;
    flex: none;
  }
  .brand-square {
    width: 46px;
    height: 46px;
    background: var(--brand-blue);
  }
  .brand-name {
    font-family: "Oswald", sans-serif;
    font-weight: 600;
    font-size: 36px;
    line-height: 1.0;
    color: var(--brand-blue);
    text-transform: uppercase;
    white-space: nowrap;
  }
  .phone-pill {
    flex: none;
    height: 88px;
    padding: 0 26px;
    border-radius: 16px;
    background: var(--brand-blue);
    color: var(--board-white);
    font-family: "Oswald", sans-serif;
    font-weight: 600;
    font-size: 58px;
    line-height: 88px;
    letter-spacing: 1px;
    white-space: nowrap;
  }
</style>
</head>
<body>
  <section class="billboard">
    <div class="porch-photo" role="img" aria-label="Screened coastal porch with wicker seating overlooking a lawn and pond"></div>
    <div class="message">
      <h1 class="headline">
        <span class="headline-top">Screen Your Porch</span>
        <span class="headline-bottom">Built for the Coast</span>
      </h1>
      <div class="contact-row">
        <div class="brand">
          <div class="brand-square"></div>
          <div class="brand-name">Tidewater<br>Screening</div>
        </div>
        <div class="phone-pill">555.014.2278</div>
      </div>
    </div>
  </section>
</body>
</html>
```